Coastline Premier Retreats Business Card Design

Design a business card for Coastline Premier Retreats. Look at the website for colors and reference. Card should have logo, name, title, office number, mobile number, email, URL and a tagline like, "Luxury Hotel & Resort Email Marketing" (This might change).

https://www.coastlinepremierretreats.example

The rest I will leave up to your imagination.

Contact Information for Business Card

Logo, name, title, office number, mobile number, email, URL and a tagline like, "Luxury Hotel & Resort Email Marketing" (This might change).

```html
<!DOCTYPE html>
<html lang="en">
<head>
<meta charset="utf-8">
<title>Coastline Premier Retreats – Business Card</title>
<link href="https://fonts.googleapis.com/css2?family=Montserrat:wght@400;500;700&display=swap" rel="stylesheet">
<style>
  :root {
    --backdrop: #262626;
    --card: #1b1b1b;
    --card-edge: #141414;
    --orange: #f07810;
    --white: #f4f4f4;
    --muted: #d9d9d9;
  }
  * { box-sizing: border-box; margin: 0; padding: 0; }
  html, body {
    width: 1200px; height: 801px; overflow: hidden;
    background: var(--backdrop);
    font-family: "Montserrat", Arial, sans-serif;
  }
  .stage {
    width: 1200px; height: 801px;
    display: flex; align-items: center; justify-content: center; gap: 50px;
  }
  .card {
    position: relative;
    width: 540px; height: 310px;
    background: linear-gradient(135deg, #222 0%, var(--card) 55%, var(--card-edge) 100%);
    box-shadow: 0 18px 40px rgba(0,0,0,.55);
    overflow: hidden;
  }
  .card::after {
    content: ""; position: absolute; left: 0; right: 0; bottom: 0;
    height: 4px; background: var(--orange);
  }

  /* brand name wordmark */
  .brand {
    display: flex; align-items: center; gap: 10px;
    color: var(--white); font-weight: 700; text-transform: uppercase;
    letter-spacing: .04em; line-height: 1.05;
  }
  .brand-square { width: 12px; height: 12px; background: var(--orange); flex: none; }

  /* front */
  .front .brand { position: absolute; top: 30px; right: 32px; font-size: 17px; }
  .identity { position: absolute; left: 40px; top: 104px; }
  .identity-bar {
    position: absolute; left: -40px; top: -4px; width: 18px; height: 30px;
    background: var(--orange);
  }
  .person-name {
    color: var(--orange); font-weight: 700; font-size: 24px;
    letter-spacing: .04em; text-transform: uppercase;
  }
  .person-title { color: var(--muted); font-size: 13px; margin-top: 2px; }
  .address { color: var(--white); font-size: 13px; line-height: 1.45; margin-top: 20px; }
  .contacts {
    position: absolute; left: 40px; bottom: 22px;
    list-style: none; color: var(--white); font-size: 12.5px; line-height: 1.55;
  }
  .contacts li { display: flex; align-items: center; gap: 8px; }
  .contacts svg { width: 11px; height: 11px; fill: var(--orange); flex: none; }
  .contacts .web-domain { color: var(--orange); }

  /* back */
  .back::before {
    content: ""; position: absolute; left: 0; top: 0; bottom: 0;
    width: 4px; background: var(--orange);
  }
  .back .brand {
    position: absolute; top: 110px; left: 0; right: 0;
    justify-content: center; font-size: 24px;
  }
  .tagline {
    position: absolute; left: 0; right: 0; top: 175px;
    text-align: center; color: var(--orange); font-size: 15px; line-height: 1.4;
  }
</style>
</head>
<body>
<main class="stage">

  <section class="card front" aria-label="Business card front">
    <div class="brand"><span class="brand-square"></span>Coastline Premier Retreats</div>

    <div class="identity">
      <span class="identity-bar"></span>
      <h1 class="person-name">Daniel Marsh</h1>
      <p class="person-title">CEO/Founder</p>
      <p class="address">Po Box, 480 Harbor Rd<br>Seaview, CA 90210</p>
    </div>

    <ul class="contacts">
      <li><svg viewBox="0 0 12 12"><path d="M3 0h6a1 1 0 0 1 1 1v10a1 1 0 0 1-1 1H3a1 1 0 0 1-1-1V1a1 1 0 0 1 1-1zm0 1.5v8h6v-8z"/></svg>555.210.4400</li>
      <li><svg viewBox="0 0 12 12"><path d="M2.5 0.5l2 2.5-1 1.3a7 7 0 0 0 4.2 4.2l1.3-1 2.5 2-1.2 2A10 10 0 0 1 0.5 1.7z"/></svg>+1 555 390 7721</li>
      <li><svg viewBox="0 0 12 12"><path d="M0 2h12v8H0zm1.2 1L6 6.6 10.8 3z"/></svg>info@coastlinepremierretreats.example</li>
      <li><svg viewBox="0 0 12 12"><circle cx="6" cy="6" r="6"/></svg>www.<span class="web-domain">coastlinepremierretreats</span>.example</li>
    </ul>
  </section>

  <section class="card back" aria-label="Business card back">
    <div class="brand"><span class="brand-square"></span>Coastline Premier Retreats</div>
    <p class="tagline">Luxury Hotel &amp; Resort<br>Email Marketing</p>
  </section>

</main>
</body>
</html>
```